Refresh Application User Interface

Brightmoor wishes to update the look of its business applications. Two representative forms are shown below. Please note, we are not considering changes in functionality or usability. Our goal is a cleaner, more contemporary design.

Industry/Entity Type

Business

```html
<!DOCTYPE html>
<html lang="en">
<head>
<meta charset="utf-8">
<title>Brightmoor – Purchase Order Lines</title>
<link href="https://fonts.googleapis.com/css2?family=Lato:wght@400;700;900&display=swap" rel="stylesheet">
<style>
:root{
  --navy:#0f2f6b;
  --navy-2:#1d4f9c;
  --blue-text:#1f4d96;
  --green:#3aa417;
  --green-text:#3aa417;
  --page:#efefef;
  --band:#f2f2f2;
  --white:#ffffff;
  --line:#c9c9c9;
  --ink:#222;
  --red:#e0211b;
  --row-alt:#e4e4e4;
  --tab:#4f7fbe;
}
*{box-sizing:border-box;margin:0;padding:0}
html,body{width:1200px;height:1160px;overflow:hidden}
body{background:var(--page);font-family:"Lato",sans-serif;color:var(--ink);position:relative}
.abs{position:absolute}
.topbar{left:0;top:0;width:1200px;height:40px;background:var(--navy);color:#fff;font-size:14px}
.topbar span{position:absolute;top:11px;white-space:nowrap}
.topbar .sep{position:absolute;top:0;width:1px;height:40px;background:#3a5a92}
.mainnav{left:0;top:40px;width:1200px;height:80px;background:var(--band)}
.mainnav a{position:absolute;top:32px;font-size:15px;font-weight:900;color:var(--navy);text-decoration:none}
.mainnav .active{position:absolute;left:290px;top:0;width:80px;height:80px;background:var(--green)}
.mainnav a.on{color:#fff}
.brand{position:absolute;left:912px;top:29px;width:189px;height:30px;background:#fff;display:flex;align-items:center;justify-content:center;gap:8px;font-size:20px;font-weight:900;color:var(--navy)}
.brand i{width:12px;height:12px;border-radius:50%;background:var(--green)}
.subnav{left:0;top:120px;width:1200px;height:49px;background:var(--green)}
.subnav a{position:absolute;top:15px;font-size:15px;color:#fff;text-decoration:none}
.subnav .pill{position:absolute;left:126px;top:11px;width:80px;height:28px;border-radius:14px;background:var(--navy)}
h1{position:absolute;left:110px;top:203px;font-size:27px;font-weight:400;color:var(--navy)}
.tabs{left:766px;top:218px;height:36px;width:324px;background:#fff}
.tabs span{position:absolute;top:11px;font-size:14px;color:#222}
.tabs .hdr{left:0;top:0;width:93px;height:36px;background:var(--tab);color:#fff;display:flex;align-items:center;justify-content:center;font-size:14px;position:absolute}
.toolbar{left:110px;top:254px;width:980px;height:54px;background:linear-gradient(#2a5eaa,#1a478f);color:#fff}
.toolbar .sep{position:absolute;top:0;width:1px;height:54px;background:#4b74b6}
.toolbar span{position:absolute;top:18px;font-size:15px;white-space:nowrap}
.toolbar svg{position:absolute}
.panel{left:110px;top:310px;width:980px;height:715px;background:#fff;box-shadow:0 1px 3px rgba(0,0,0,.2)}
.orderbox{left:138px;top:332px;width:923px;height:104px;background:#fff;box-shadow:0 1px 4px rgba(0,0,0,.25)}
.orderbox span{position:absolute;font-size:14px}
.gridbar{left:135px;top:473px;width:923px;height:32px;background:linear-gradient(#2a5eaa,#1a478f);color:#fff}
.gridbar .sep{position:absolute;top:0;width:1px;height:32px;background:#4b74b6}
.gridbar svg{position:absolute}
.gridhead{left:135px;top:505px;width:923px;height:37px;background:var(--green);color:#fff}
.gridhead span{position:absolute;top:10px;font-size:15px}
.cb{position:absolute;width:20px;height:20px;background:#fff;border:1px solid #999}
.gridbody{left:135px;top:542px;width:923px;height:424px;background:#fff;border:1px solid var(--line);border-top:none}
.row{position:absolute;left:0;width:921px;height:141px;border-bottom:1px solid var(--line)}
.row.alt{background:var(--row-alt)}
.row .f{position:absolute;height:28px;border:1px solid #aaa;background:#fff;font-size:12px;padding:7px 12px;white-space:nowrap;overflow:hidden}
.row .sel::after{content:"";position:absolute;right:12px;top:8px;width:7px;height:7px;border-right:1.5px solid #555;border-bottom:1.5px solid #555;transform:rotate(45deg)}
.row .t{position:absolute;font-size:13px;white-space:nowrap}
.row .num{position:absolute;font-size:16px}
.blue{color:var(--blue-text)}
.red{color:var(--red)}
.cal{position:absolute;width:24px;height:24px;border:1px solid #888;background:#fff;font-size:8px;text-align:center;line-height:9px;padding-top:2px;color:var(--navy)}
.cal b{display:block;font-size:10px;font-weight:700;border-top:1px solid #888;margin-top:1px;line-height:11px}
.hint{left:0;top:983px;width:1200px;text-align:center;font-size:15px;color:var(--blue-text)}
.footline{left:110px;top:1093px;width:980px;height:1px;background:#777}
.copy{left:0;top:1113px;width:1200px;text-align:center;font-size:14px;color:#555}
</style>
</head>
<body>

<div class="abs topbar">
  <span style="left:114px">Logged in As Dana Hale ⚙</span>
  <span style="left:325px">Current Role: Administrator ›</span>
  <span style="left:793px">Touch</span><i class="sep" style="left:842px"></i>
  <span style="left:855px">New Tab</span><i class="sep" style="left:924px"></i>
  <span style="left:934px">Help</span><i class="sep" style="left:980px"></i>
  <span style="left:987px">Support</span><i class="sep" style="left:1054px"></i>
  <span style="left:1062px">Log Out</span>
</div>

<nav class="abs mainnav">
  <div class="active"></div>
  <a style="left:130px">HOME</a>
  <a style="left:209px">ESOURCE</a>
  <a class="on" style="left:311px">EBUY</a>
  <a style="left:383px">EREQUEST</a>
  <a style="left:492px">ESELL</a>
  <a style="left:567px">ESTOCK</a>
  <a style="left:659px">EPLAN</a>
  <a style="left:741px">PREFRENCES</a>
  <div class="brand"><i></i>Brightmoor</div>
</nav>

<nav class="abs subnav">
  <div class="pill"></div>
  <a style="left:144px">Orders</a>
  <a style="left:226px">Receipts</a>
  <a style="left:313px">Shipments</a>
  <a style="left:413px">Invoice</a>
  <a style="left:491px">Pricing</a>
  <a style="left:567px">Tables</a>
  <a style="left:639px">Reports</a>
  <a style="left:725px">Inquiries</a>
  <a style="left:813px">Periodic Tasks</a>
  <a style="left:937px">Workflows</a>
</nav>

<h1>Purchase Order Lines</h1>

<div class="abs tabs">
  <div class="hdr">HEADER</div>
  <span style="left:112px">LINES</span>
  <svg class="abs" style="left:146px;top:2px" width="14" height="14" viewBox="0 0 14 14"><circle cx="7" cy="7" r="6" fill="none" stroke="#3aa417" stroke-width="1.4"/><path d="M4 7l2 2 4-4" fill="none" stroke="#3aa417" stroke-width="1.4"/></svg>
  <span style="left:173px">CHARGES</span>
  <span style="left:257px">NOTES</span>
  <svg class="abs" style="left:303px;top:2px" width="14" height="14" viewBox="0 0 14 14"><circle cx="7" cy="7" r="6" fill="none" stroke="#3aa417" stroke-width="1.4"/><path d="M4 7l2 2 4-4" fill="none" stroke="#3aa417" stroke-width="1.4"/></svg>
</div>

<div class="abs toolbar">
  <svg style="left:18px;top:15px" width="26" height="26" viewBox="0 0 24 24" fill="none" stroke="#fff" stroke-width="2"><path d="M20 11l-8 8a5 5 0 01-7-7l9-9a3.5 3.5 0 015 5l-9 9a2 2 0 01-3-3l8-8"/></svg>
  <i class="sep" style="left:55px"></i>
  <svg style="left:68px;top:14px" width="26" height="26" viewBox="0 0 24 24" fill="none" stroke="#fff" stroke-width="1.8"><path d="M6 2h9l5 5v15H8"/><path d="M15 2v5h5"/><circle cx="7" cy="16" r="3.5"/><path d="M4.5 18.5L2 21"/></svg>
  <i class="sep" style="left:105px"></i>
  <svg style="left:121px;top:14px" width="26" height="26" viewBox="0 0 24 24" fill="#fff" stroke="#fff" stroke-width="2"><circle cx="5" cy="4" r="2.5"/><circle cx="19" cy="4" r="2.5"/><circle cx="5" cy="20" r="2.5"/><circle cx="19" cy="20" r="2.5"/><path d="M5 4v16M5 4l14 16M19 4v16" fill="none"/></svg>
  <i class="sep" style="left:161px"></i>
  <svg style="left:174px;top:15px" width="26" height="24" viewBox="0 0 24 22" fill="none" stroke="#fff" stroke-width="1.8"><rect x="1" y="2" width="22" height="5"/><path d="M3 7v13h18V7M9 11h6"/></svg>
  <i class="sep" style="left:212px"></i>
  <svg style="left:221px;top:14px" width="26" height="26" viewBox="0 0 24 24"><circle cx="12" cy="12" r="11" fill="#fff"/><text x="12" y="17" text-anchor="middle" font-family="Lato,sans-serif" font-weight="900" font-size="15" fill="#1d4f9c">?</text></svg>
  <i class="sep" style="left:253px"></i>
  <svg style="left:264px;top:15px" width="22" height="22" viewBox="0 0 24 24" fill="#fff"><path d="M21 6a5 5 0 01-7 5L5 20a2 2 0 01-3-3l9-9a5 5 0 015-7l-3 3 1 3 3 1z"/></svg>
  <span style="left:287px">View GL account</span>
  <svg style="left:412px;top:12px" width="26" height="30" viewBox="0 0 24 28" fill="none" stroke="#fff" stroke-width="1.8"><path d="M4 2h10l6 6v18H4z"/><circle cx="14" cy="17" r="4"/><path d="M14 15v4M12 17h4"/></svg>
  <span style="left:442px">Post Order</span>
  <svg style="left:552px;top:21px" width="14" height="14" viewBox="0 0 14 14" fill="none" stroke="#fff" stroke-width="2.2"><circle cx="6" cy="6" r="4.5"/><path d="M9 9l4 4"/></svg>
  <span style="left:570px">SEARCH</span>
  <svg style="left:640px;top:19px" width="18" height="16" viewBox="0 0 18 16" fill="none" stroke="#fff" stroke-width="1.5"><rect x="1" y="1" width="16" height="14"/><path d="M4 5h2M8 5h6M4 8h2M8 8h6M4 11h2M8 11h6"/></svg>
  <span style="left:661px">NEWS</span>
  <svg style="left:724px;top:19px" width="17" height="17" viewBox="0 0 18 18" fill="none" stroke="#fff" stroke-width="1.6"><circle cx="9" cy="9" r="8"/><path d="M5 9l3 3 5-6"/></svg>
  <span style="left:745px">APPLY</span>
  <svg style="left:806px;top:19px" width="17" height="17" viewBox="0 0 18 18" fill="none" stroke="#fff" stroke-width="1.6"><rect x="1" y="1" width="16" height="16"/><path d="M5 5l8 8M13 5l-8 8"/></svg>
  <span style="left:827px">DELETE</span>
  <svg style="left:893px;top:19px" width="17" height="17" viewBox="0 0 18 18" fill="none" stroke="#fff" stroke-width="1.6"><circle cx="9" cy="9" r="8"/><path d="M13 9H6M9 5L5 9l4 4"/></svg>
  <span style="left:914px">BACK</span>
</div>

<div class="abs panel"></div>

<div class="abs orderbox">
  <span style="left:42px;top:14px;font-size:16px">Order#</span>
  <span style="left:133px;top:14px">100159</span>
  <span style="left:304px;top:13px;font-size:15px;color:var(--green-text)">Regular Purchase Order</span>
  <span style="left:770px;top:17px;font-size:15px;color:var(--blue-text)">Hold for Completion</span>
  <span style="left:133px;top:50px">Harbor Clinical Supply, Westbrook MA</span>
</div>

<div class="abs gridbar">
  <svg style="left:14px;top:7px" width="18" height="19" viewBox="0 0 18 19" fill="none" stroke="#fff" stroke-width="1.8"><path d="M16 2H2l7 7.5L2 17h14"/></svg>
  <i class="sep" style="left:42px"></i>
  <svg style="left:50px;top:6px" width="20" height="20" viewBox="0 0 20 20" fill="none" stroke="#fff" stroke-width="1.5"><rect x="2" y="1" width="9" height="12"/><rect x="8" y="6" width="9" height="12" fill="#1d4f9c"/></svg>
  <i class="sep" style="left:77px"></i>
  <svg style="left:85px;top:6px" width="17" height="20" viewBox="0 0 16 20" fill="#fff"><rect x="1" y="3" width="14" height="16" rx="1"/><rect x="5" y="1" width="6" height="4" rx="1" stroke="#1d4f9c"/><path d="M4 9h8M4 12h8M4 15h8" stroke="#1d4f9c" stroke-width="1.4"/></svg>
  <i class="sep" style="left:106px"></i>
  <svg style="left:116px;top:8px" width="17" height="17" viewBox="0 0 16 16" fill="#fff"><path d="M0 1h16l-6 7v7l-4-2V8z"/></svg>
  <i class="sep" style="left:141px"></i>
  <svg style="left:169px;top:9px" width="16" height="15" viewBox="0 0 16 15" fill="none" stroke="#fff" stroke-width="1.5"><rect x="1" y="1" width="14" height="13"/><path d="M5 4.5l6 6M11 4.5l-6 6"/></svg>
  <svg style="left:739px;top:10px" width="30" height="13" viewBox="0 0 30 13" fill="#5a84c8"><rect x="0" y="1" width="2" height="11"/><path d="M12 1v11L3 6.5z"/></svg>
  <svg style="left:762px;top:10px" width="24" height="13" viewBox="0 0 24 13" fill="#5a84c8"><path d="M10 1v11L1 6.5zM20 1v11l-9-5.5z"/></svg>
  <span class="abs" style="left:791px;top:9px;font-size:12px;font-weight:700">Page 1 &nbsp;of 1</span>
  <svg style="left:862px;top:10px" width="24" height="13" viewBox="0 0 24 13" fill="#5a84c8"><path d="M1 1v11l9-5.5zM11 1v11l9-5.5z"/></svg>
  <svg style="left:892px;top:10px" width="16" height="13" viewBox="0 0 16 13" fill="#5a84c8"><path d="M1 1v11l9-5.5z"/><rect x="11" y="1" width="2" height="11"/></svg>
</div>

<div class="abs gridhead">
  <span style="left:26px">Line#</span>
  <span style="left:97px">Product</span>
  <span style="left:225px">Supplier Part#</span>
  <span style="left:366px">Open Qty</span>
  <span style="left:465px">Unit</span>
  <span style="left:563px">Unit Price</span>
  <span style="left:663px">Extended</span>
  <span style="left:760px">LI Type /Ship To</span>
  <div class="cb" style="left:886px;top:9px"></div>
</div>

<div class="abs gridbody">
  <div class="row" style="top:0">
    <span class="num" style="left:27px;top:36px">10</span>
    <div class="f" style="left:84px;top:28px;width:126px">P-1200</div>
    <svg class="abs" style="left:216px;top:34px" width="18" height="18" viewBox="0 0 18 18" fill="none" stroke="#999" stroke-width="2"><circle cx="7" cy="7" r="5.5"/><path d="M11 11l5 5"/></svg>
    <div class="cb" style="left:250px;top:33px"></div>
    <div class="f" style="left:360px;top:28px;width:83px">01</div>
    <div class="f sel" style="left:459px;top:28px;width:82px">EA</div>
    <div class="f" style="left:562px;top:28px;width:83px">$6.50</div>
    <span class="num blue" style="left:668px;top:36px;font-weight:700;font-size:15px">$6.50</span>
    <div class="f sel" style="left:743px;top:26px;width:126px">Receive &amp; Pay</div>
    <div class="cb" style="left:884px;top:26px"></div>
    <div class="f" style="left:84px;top:64px;width:561px">Fennwick 389317 - Brochure Paper, Ultra Smooth Text, 8 1/2" x 11", 28lb, 96 Brightness</div>
    <span class="t blue" style="left:668px;top:70px;font-size:15px">ALCH</span>
    <div class="f sel" style="left:744px;top:64px;width:127px"></div>
    <span class="t" style="left:83px;top:107px">On Purchase Order <span class="blue" style="font-size:15px">&nbsp;30</span></span>
    <span class="t" style="left:360px;top:105px">Available <span class="blue" style="font-size:15px">&nbsp;0</span></span>
    <span class="t red" style="left:554px;top:103px;text-decoration:underline">Over Budget</span>
    <span class="t red" style="left:665px;top:103px">Pending</span>
    <svg class="abs" style="left:758px;top:102px" width="24" height="20" viewBox="0 0 24 20" fill="none" stroke="#1d4f9c" stroke-width="1.8"><rect x="1" y="4" width="15" height="14" rx="3"/><path d="M10 12l10-10 2 2-10 10-3 1z" fill="#1d4f9c"/></svg>
    <div class="cal" style="left:808px;top:102px">Aur<b>22</b></div>
  </div>

  <div class="row alt" style="top:141px;height:134px">
    <span class="num" style="left:22px;top:36px">20</span>
    <div class="f" style="left:79px;top:28px;width:126px">P-1100</div>
    <svg class="abs" style="left:211px;top:34px" width="18" height="18" viewBox="0 0 18 18" fill="none" stroke="#999" stroke-width="2"><circle cx="7" cy="7" r="5.5"/><path d="M11 11l5 5"/></svg>
    <div class="cb" style="left:245px;top:32px"></div>
    <div class="f" style="left:355px;top:28px;width:83px">01</div>
    <div class="f sel" style="left:454px;top:28px;width:82px">EA</div>
    <div class="f" style="left:557px;top:28px;width:83px">$5.00</div>
    <span class="num blue" style="left:663px;top:36px;font-weight:700;font-size:15px">$5.00</span>
    <div class="f sel" style="left:738px;top:26px;width:126px">Receive &amp; Pay</div>
    <div class="cb" style="left:879px;top:26px"></div>
    <div class="f" style="left:79px;top:64px;width:561px">Polar Crest 454230 - Recycled Laser Paper 1 case(2,500 count) - 241b, 90 bright</div>
    <span class="t blue" style="left:663px;top:70px;font-size:15px">ALCH</span>
    <div class="f sel" style="left:739px;top:64px;width:127px"></div>
    <span class="t" style="left:78px;top:107px">On Purchase Order <span class="blue" style="font-size:15px">&nbsp;170</span></span>
    <span class="t" style="left:355px;top:104px">Available <span class="blue" style="font-size:15px">&nbsp;0</span></span>
    <span class="t red" style="left:549px;top:103px;text-decoration:underline">Over Budget</span>
    <span class="t red" style="left:660px;top:103px">Pending</span>
    <svg class="abs" style="left:753px;top:102px" width="24" height="20" viewBox="0 0 24 20" fill="none" stroke="#1d4f9c" stroke-width="1.8"><rect x="1" y="4" width="15" height="14" rx="3"/><path d="M10 12l10-10 2 2-10 10-3 1z" fill="#1d4f9c"/></svg>
    <div class="cal" style="left:803px;top:102px">Aur<b>22</b></div>
  </div>
</div>

<div class="abs hint">Click Search, or Enter Property Value and Click apply</div>
<div class="abs footline"></div>
<div class="abs copy">© 2018 Company Name &nbsp;All right reserved &nbsp;Terms of Use</div>

</body>
</html>
```